Essential Oil 15ml - package of 6

Design of a box of 6 different essential oils.
+ design of the bottle stickers
My bottles are 15ml clear blue glass.

The pictures attached are my competitors...

Target Market(s)

TERVIK USA

Font styles to use
Serif

Requirements
Must have
• Our logo + "essential oil" and type (lavender, eucalyptus etc....)
• 15ml - 0.50 fl.oz.
• special color for the oil type.

```html
<!DOCTYPE html>
<html lang="en">
<head>
<meta charset="utf-8">
<title>Oren Vale Essential Oil Labels</title>
<link rel="stylesheet" href="https://fonts.googleapis.com/css2?family=Cinzel:wght@400;500&family=Marcellus&display=swap">
<style>
  :root {
    --page-bg: #ffffff;
    --panel-dark: #1c1c2a;
    --panel-dark-2: #262638;
    --brand-gold: #c98a22;
    --text-dark: #1a1420;
    --rose-top: #e0125a;
    --rose-bottom: #5a1030;
    --lavender-top: #8a10d8;
    --lavender-bottom: #2a0a5a;
    --eucalyptus-top: #3aa8d8;
    --eucalyptus-bottom: #0a3a5a;
    --lemon-top: #e8e018;
    --lemon-bottom: #3a3a08;
    --apple-top: #4ef01a;
    --apple-bottom: #0e3a10;
    --lime-top: #9cf01a;
    --lime-bottom: #1a4a10;
    --name-rose: #e8a23a;
    --name-lavender: #d0902c;
    --name-eucalyptus: #22e6f2;
    --name-lemon: #c8901a;
    --name-apple: #d8682a;
    --name-lime: #c8561e;
  }
  * { margin: 0; padding: 0; box-sizing: border-box; }
  html, body { width: 1200px; height: 570px; overflow: hidden; background: var(--page-bg); }
  .sheet { position: relative; width: 1200px; height: 570px; }
  .label {
    position: absolute; width: 206px; height: 132px; display: flex;
    border-radius: 6px 22px 22px 6px; overflow: hidden;
  }
  .label__info {
    width: 124px; height: 100%; display: flex; flex-direction: column;
    align-items: center; justify-content: center; text-align: center;
    font-family: "Cinzel", "Marcellus", serif; color: var(--text-dark);
    background: linear-gradient(180deg, var(--top) 0%, var(--top) 45%, var(--bottom) 100%);
  }
  .label__kicker { font-size: 10px; letter-spacing: 0.2px; }
  .label__name { font-size: 15px; margin: 8px 0 9px; color: var(--name); }
  .label__grade { font-size: 10px; line-height: 1.1; }
  .label__volume { font-size: 7px; margin-top: 6px; }
  .label__brand {
    flex: 1; display: flex; align-items: center; justify-content: space-between;
    padding: 0 10px 0 4px;
    background: linear-gradient(180deg, var(--panel-dark-2), var(--panel-dark));
  }
  .brand-name {
    writing-mode: vertical-rl; font-family: "Marcellus", serif;
    font-size: 19px; color: var(--brand-gold); letter-spacing: 0.5px;
  }
  .brand-dot { width: 28px; height: 28px; border-radius: 50%; background: var(--brand-gold); }
  .label--rose { left: 126px; top: 60px; --top: var(--rose-top); --bottom: var(--rose-bottom); --name: var(--name-rose); }
  .label--lavender { left: 650px; top: 60px; --top: var(--lavender-top); --bottom: var(--lavender-bottom); --name: var(--name-lavender); }
  .label--eucalyptus { left: 126px; top: 220px; --top: var(--eucalyptus-top); --bottom: var(--eucalyptus-bottom); --name: var(--name-eucalyptus); }
  .label--lemon { left: 650px; top: 220px; --top: var(--lemon-top); --bottom: var(--lemon-bottom); --name: var(--name-lemon); }
  .label--apple { left: 126px; top: 380px; --top: var(--apple-top); --bottom: var(--apple-bottom); --name: var(--name-apple); }
  .label--lime { left: 650px; top: 380px; --top: var(--lime-top); --bottom: var(--lime-bottom); --name: var(--name-lime); }
</style>
</head>
<body>
<main class="sheet">
  <section class="label label--rose">
    <div class="label__info"><p class="label__kicker">100% Essential Oil</p><p class="label__name">ROSE</p><p class="label__grade">PURE THERAPEUTIC<br>GRADE</p><p class="label__volume">15 ML</p></div>
    <div class="label__brand"><span class="brand-name">Oren Vale</span><span class="brand-dot"></span></div>
  </section>
  <section class="label label--lavender">
    <div class="label__info"><p class="label__kicker">100% Essential Oil</p><p class="label__name">LAVANDER</p><p class="label__grade">PURE THERAPEUTIC<br>GRADE</p><p class="label__volume">15 ML</p></div>
    <div class="label__brand"><span class="brand-name">Oren Vale</span><span class="brand-dot"></span></div>
  </section>
  <section class="label label--eucalyptus">
    <div class="label__info"><p class="label__kicker">100% Essential Oil</p><p class="label__name">EUCALYPTUS</p><p class="label__grade">PURE THERAPEUTIC<br>GRADE</p><p class="label__volume">15 ML</p></div>
    <div class="label__brand"><span class="brand-name">Oren Vale</span><span class="brand-dot"></span></div>
  </section>
  <section class="label label--lemon">
    <div class="label__info"><p class="label__kicker">100% Essential Oil</p><p class="label__name">LEMON</p><p class="label__grade">PURE THERAPEUTIC<br>GRADE</p><p class="label__volume">15 ML</p></div>
    <div class="label__brand"><span class="brand-name">Oren Vale</span><span class="brand-dot"></span></div>
  </section>
  <section class="label label--apple">
    <div class="label__info"><p class="label__kicker">100% Essential Oil</p><p class="label__name">APPLE</p><p class="label__grade">PURE THERAPEUTIC<br>GRADE</p><p class="label__volume">15 ML</p></div>
    <div class="label__brand"><span class="brand-name">Oren Vale</span><span class="brand-dot"></span></div>
  </section>
  <section class="label label--lime">
    <div class="label__info"><p class="label__kicker">100% Essential Oil</p><p class="label__name">LIME</p><p class="label__grade">PURE THERAPEUTIC<br>GRADE</p><p class="label__volume">15 ML</p></div>
    <div class="label__brand"><span class="brand-name">Oren Vale</span><span class="brand-dot"></span></div>
  </section>
</main>
</body>
</html>
```